Heron Property Inspection business card

I am the principal inspector of Heron Property Inspections. I serve Northern Virginia from Winchester to Arlington.Associate, Federated Guild of Dwelling Examiners (FGDE)Graduate, FGDE Home Inspectors CourseNational Association of Home Inspectors ExamI'd like the business card to look more professional than comical.I pulled the attached picture off the web. I'd like to have something like that or an image of a house as my logo on the cards.

Target Market(s)

Persons who recently purchased a home.

Industry/Entity Type

Business

Contact Information for Business Card

Bob AllenBadger Home Inspections, LLC.4455 River RoadBluemont, Virginia 20135cell: 703-231-6680e-mail: tkmarlow@postvale.net

Font styles to use
Serif
Sans Serif

Requirements
Must have
• I'd like to have a logo, something that identifies me as a home inspector. The attached images are something that I'd like to have incorporated into my business card logo.
Nice to have
• I'd like a sketch of a house and/or a magnifying glass showing a house being inspected. The attached images are used as a suggestion only, I do not own the images.
Should not have
• Gimmicky stuff. I want to appear professional and trustworthy.

```html
<!DOCTYPE html>
<html lang="en">
<head>
<meta charset="utf-8">
<title>Heron Property Inspections — Business Card</title>
<link rel="stylesheet" href="https://fonts.googleapis.com/css2?family=Roboto:wght@300;400;700&display=swap">
<style>
  :root {
    --backdrop: #e9eaec;
    --card: #ffffff;
    --navy: #2d56ad;
    --navy-deep: #1f3f8f;
    --cyan: #24b9d6;
    --cyan-light: #3ccbe4;
    --ink: #2f58ad;
    --white: #ffffff;
  }
  * { margin: 0; padding: 0; box-sizing: border-box; }
  html, body {
    width: 1200px; height: 892px; overflow: hidden;
    background: var(--backdrop);
    font-family: "Roboto", Arial, sans-serif;
  }
  .business-card {
    position: absolute; left: 100px; top: 160px;
    width: 1000px; height: 572px;
    background: var(--card);
    overflow: hidden;
    box-shadow: 0 6px 24px rgba(0,0,0,.12);
  }
  .card-bands { position: absolute; inset: 0; }
  .brand {
    position: absolute; left: 70px; top: 170px;
    display: flex; align-items: center; gap: 24px;
    color: var(--ink); font-weight: 700;
  }
  .brand-mark {
    width: 72px; height: 72px; border-radius: 50%;
    background: var(--cyan); flex: none;
  }
  .brand-name { font-size: 44px; line-height: 1.18; }
  .contact-list {
    position: absolute; left: 150px; top: 388px;
    list-style: none; color: var(--white);
    font-weight: 300; font-size: 22px; line-height: 1;
  }
  .contact-item { display: flex; align-items: center; gap: 14px; margin-bottom: 18px; }
  .contact-icon { width: 22px; height: 22px; flex: none; }
  .employee {
    position: absolute; right: 44px; top: 374px;
    color: var(--white); text-align: right;
  }
  .employee-name { font-size: 42px; font-weight: 400; line-height: 1.1; }
  .employee-title { font-size: 20px; font-weight: 300; margin-top: 4px; }
</style>
</head>
<body>
  <article class="business-card">
    <svg class="card-bands" width="1000" height="572" viewBox="0 0 1000 572" aria-hidden="true">
      <defs>
        <linearGradient id="cyanBand" x1="0" y1="0" x2="1" y2="1">
          <stop offset="0" stop-color="#3ccbe4"/>
          <stop offset="1" stop-color="#24b9d6"/>
        </linearGradient>
        <linearGradient id="navyBand" x1="0" y1="0" x2="1" y2="1">
          <stop offset="0" stop-color="#2d56ad"/>
          <stop offset="1" stop-color="#1f3f8f"/>
        </linearGradient>
      </defs>
      <polygon class="band-cyan" points="50,340 600,340 730,572 0,572" fill="url(#cyanBand)"/>
      <polygon class="band-navy" points="614,340 1000,340 1000,572 744,572" fill="url(#navyBand)"/>
    </svg>

    <div class="brand">
      <span class="brand-mark"></span>
      <p class="brand-name">Tim Marlow Heron<br>Property Inspections, LLC</p>
    </div>

    <ul class="contact-list">
      <li class="contact-item">
        <svg class="contact-icon" viewBox="0 0 24 24"><rect x="2" y="2" width="20" height="20" rx="5" fill="#fff"/><rect x="8" y="6" width="8" height="12" rx="1.5" fill="none" stroke="#24b9d6" stroke-width="1.8"/></svg>
        <span>703-555-0192</span>
      </li>
      <li class="contact-item">
        <svg class="contact-icon" viewBox="0 0 24 24"><rect x="2" y="2" width="20" height="20" rx="5" fill="#fff"/><rect x="6" y="8" width="12" height="8" fill="none" stroke="#24b9d6" stroke-width="1.6"/><path d="M6 8l6 5 6-5" fill="none" stroke="#24b9d6" stroke-width="1.6"/></svg>
        <span>tkmarlow@postvale.net</span>
      </li>
      <li class="contact-item">
        <svg class="contact-icon" viewBox="0 0 24 24"><rect x="2" y="2" width="20" height="20" rx="5" fill="#fff"/><path d="M12 18s-4-4.5-4-7.5a4 4 0 0 1 8 0C16 13.5 12 18 12 18z" fill="#24b9d6"/><circle cx="12" cy="10.5" r="1.5" fill="#fff"/></svg>
        <span>7182 Quarry Lane Fernhill, Virginia 20148</span>
      </li>
    </ul>

    <div class="employee">
      <p class="employee-name">Employee name</p>
      <p class="employee-title">Managing Director</p>
    </div>
  </article>
</body>
</html>
```